Brintel Works - Fast, Efficient and Gas Mainteance for Domestic, Commercial and Industrial clients

We are in the process of purchasing a new business and would like to get a new logo and business card.
Business is a gas maintenance business that also does new gas installations.
Has been established since 1988.
Services include:
Install all types of gas appliances & equipment inc. hot water units
Maintain / repair / replace all types of gas appliances & equipment

Target Market(s)

Domestic, Commercial and Industrial clients

Industry/Entity Type

Business

Contact Information for Business Card

admin@brintelworks.com.au
07 3918 4726
Brintel Works PTY LTD

Logo Text

Gas Fitting & Plumbing Maintenance Specialists

Font styles to use
Sans Serif

Requirements
Must have
• Logo
• Business name, contact number, email address, web address
• Domestic | Commercial | Industrial Est Since 1988
Nice to have
• Possibly a black card with a flame logo to one side
Should not have
• Spelling errors

```html
<!DOCTYPE html>
<html lang="en">
<head>
<meta charset="utf-8">
<title>Brintel Works — Business Card</title>
<link href="https://fonts.googleapis.com/css2?family=Arimo:wght@400;700&display=swap" rel="stylesheet">
<style>
  :root {
    --backdrop: #d8c3a1;
    --card: #000000;
    --brand: #e8632a;
    --ink-light: #ffffff;
    --ink-muted: #b5b5b5;
    --tab: #ffffff;
    --icon: #000000;
  }
  html, body {
    margin: 0;
    padding: 0;
    width: 1200px;
    height: 1200px;
    overflow: hidden;
    background: var(--backdrop);
    font-family: "Arimo", Arial, sans-serif;
  }
  .canvas {
    position: relative;
    width: 1200px;
    height: 1200px;
  }
  .card {
    position: absolute;
    left: 186px;
    width: 828px;
    height: 459px;
    background: var(--card);
    border-radius: 34px;
    overflow: hidden;
  }
  .card--front { top: 116px; }
  .card--back { top: 656px; }

  .front-name {
    position: absolute;
    left: 0;
    right: 0;
    top: 190px;
    text-align: center;
    font-weight: 700;
    font-size: 64px;
    line-height: 1;
    color: var(--brand);
    letter-spacing: 1px;
    margin: 0;
  }

  .identity {
    position: absolute;
    left: 94px;
    top: 160px;
    width: 224px;
    text-align: center;
  }
  .identity__name {
    margin: 0;
    font-weight: 700;
    font-size: 33px;
    line-height: 1;
    color: var(--brand);
    white-space: nowrap;
  }
  .identity__legal {
    margin: 16px 0 0;
    font-size: 18px;
    color: var(--ink-light);
    letter-spacing: 0.5px;
    white-space: nowrap;
  }
  .identity__tagline {
    margin: 12px 0 0;
    font-size: 9.6px;
    color: var(--ink-muted);
    white-space: nowrap;
  }

  .contacts {
    position: absolute;
    right: 80px;
    top: 138px;
    margin: 0;
    padding: 0;
    list-style: none;
    text-align: right;
  }
  .contacts li {
    height: 51px;
    font-size: 22.5px;
    line-height: 24px;
    color: var(--ink-light);
    letter-spacing: 0.6px;
    white-space: nowrap;
  }

  .icon-tab {
    position: absolute;
    right: 0;
    top: 78px;
    width: 64px;
    height: 300px;
    background: var(--tab);
    border-radius: 16px 0 0 16px;
  }
  .icon-tab svg {
    position: absolute;
    left: 0;
    top: 0;
  }
</style>
</head>
<body>
<main class="canvas">

  <section class="card card--front" aria-label="Card front">
    <p class="front-name">Brintel Works</p>
  </section>

  <section class="card card--back" aria-label="Card back">
    <div class="identity">
      <p class="identity__name">Brintel Works</p>
      <p class="identity__legal">Brintel Works PTY LTD</p>
      <p class="identity__tagline">Domestic | Commercial | Industrial Est Since 1988</p>
    </div>

    <ul class="contacts">
      <li>Adress 01, Adress, City.</li>
      <li>07 3918 4726</li>
      <li>admin@brintelworks.com.au</li>
      <li>www.brintelworks.com.au</li>
    </ul>

    <div class="icon-tab">
      <svg width="64" height="300" viewBox="0 0 64 300" aria-hidden="true">
        <g stroke="#000" stroke-width="1">
          <line x1="0" y1="93" x2="44" y2="93"/>
          <line x1="0" y1="145" x2="44" y2="145"/>
          <line x1="0" y1="197" x2="44" y2="197"/>
          <line x1="0" y1="249" x2="44" y2="249"/>
        </g>
        <!-- home -->
        <path d="M16 60 L28 50 L40 60 L37 60 L37 70 L31 70 L31 64 L25 64 L25 70 L19 70 L19 60 Z" fill="var(--icon)"/>
        <!-- phone -->
        <path d="M19 104 q-3 2 -1 8 q3 9 10 14 q4 2 6 -1 l1 -2 q0 -1 -1 -2 l-4 -3 q-1 -1 -2 0 l-1 1 q-4 -3 -6 -8 l1 -1 q1 -1 0 -2 l-2 -4 q-1 -1 -2 0 Z" fill="var(--icon)"/>
        <!-- at sign -->
        <g fill="none" stroke="var(--icon)" stroke-width="2.6">
          <circle cx="27" cy="170" r="4.5"/>
          <path d="M31.5 166 v6 q0 3 3 3 q3 0 3 -5 a10.5 10.5 0 1 0 -4 8.5"/>
        </g>
        <!-- globe -->
        <g fill="none" stroke="var(--icon)" stroke-width="2">
          <circle cx="27" cy="222" r="11"/>
          <ellipse cx="27" cy="222" rx="5" ry="11"/>
          <line x1="27" y1="211" x2="27" y2="233"/>
          <line x1="16" y1="222" x2="38" y2="222"/>
          <line x1="18" y1="216" x2="36" y2="216"/>
          <line x1="18" y1="228" x2="36" y2="228"/>
        </g>
      </svg>
    </div>
  </section>

</main>
</body>
</html>
```